Cover for a book about building companies without hierarchy

We need to design the cover of our new book. In 2018 we have developed a new organizational design called "Velmorith" which mean equal, just in Latin. This organizational design is hierarchy-free, and it is formed by a radial network of self-organizing teams, where people can take decisions pertaining their job, be autonomous, and contribute to the well being of the larger organization. We published a book in 2018 (see the cover attached), titled: "Velmorith. The Open People-first Structural Model to Flourish in a Shifting Era", where we used the graphic representation of the Velmorith structure in the cover (see attached). The book is intended for top managers, entrepreneurs, businesses.
After 5 years from its launch, we implemented this design in a number of companies and we learned a lot about what works and the challenges. So we decided to publish another book that will be titled: "Velmorith. 5 pillars to shape a people-first office" where we present a revised model, we focus on the principles behind Velmorith and we tell the story of the implementation of Velmorith in Corvellan Italy.
The book cover design must include both front and back, using the template attached.
In the front we need to include: an image or illustration, the Names of the authors (Marisa Tolvengo and Lorenzo Brucani) and the Pelvaro logo.
In the back we shall include: an empty space for the ISDN code as in the template, a short description of the book, the pictures and short bios of the authors .
In the spine we shall include: the title and authors.
Here's the bios:
Marisa Tolvengo is a partner at Pelvaro, a global organizational development firm, a former executive in the corporate setting (including Brindle & Moss and Quibbit! Inc.) and Past President of WPN Global (Worldwide Practitioner Network). She is the author of the book “Inner Compass. The Road to Renewing Guidance” and a FORAx speaker.
Lorenzo Brucani is a partner at Pelvaro and a former manager in multinational settings. He is the co-author of the Calloway Management Journal articles “Why Your Inner Climate Shapes your Output”, “3 Ways to Lift a Gloomy Day”, “Preparing Your Inner Climate for a Holiday Break” and “An Easy Method to Ease Lasting Tension”.
Pictures of the authors attached.
The final versions of the book cover shall be:
- book cover for paperback in English (front and back)
- Book cover for paperback in Italian (front and back)
- Book cover for kindle (only front)

```html
<!DOCTYPE html>
<html lang="en">
<head>
<meta charset="utf-8">
<title>Velmorith – Book Cover Spread</title>
<link rel="stylesheet" href="https://fonts.googleapis.com/css2?family=Encode+Sans+Condensed:wght@200;300&family=Poppins:ital,wght@0,300;0,400;0,600;1,300&display=swap">
<style>
  :root {
    --stage: #282828;
    --lilac-top: #c3b4fb;
    --lilac-mid: #d9c8fc;
    --lilac-bottom: #f3dffc;
    --ink: #111111;
    --navy: #140b4d;
    --white: #ffffff;
    --brand: #3a2f91;
    --photo-warm-a: #e7c9b8;
    --photo-warm-b: #c4584f;
    --photo-brick-a: #9a6a55;
    --photo-brick-b: #eae6e3;
  }
  * { box-sizing: border-box; margin: 0; padding: 0; }
  html, body {
    width: 1200px; height: 1200px; overflow: hidden;
    background: var(--stage);
  }
  .spread {
    position: absolute; left: 27px; top: 187px;
    width: 1146px; height: 826px;
    background: linear-gradient(180deg, var(--lilac-top) 0%, var(--lilac-mid) 45%, var(--lilac-bottom) 100%);
    overflow: hidden;
    font-family: "Poppins", sans-serif;
    color: var(--ink);
  }
  .network {
    position: absolute;
    background:
      radial-gradient(circle at 30% 40%, rgba(230,20,90,.45) 0 12%, transparent 24%),
      radial-gradient(circle at 62% 35%, rgba(108,192,74,.5) 0 10%, transparent 22%),
      radial-gradient(circle at 50% 60%, rgba(245,230,0,.6) 0 22%, transparent 48%),
      radial-gradient(circle at 78% 70%, rgba(30,144,214,.35) 0 10%, transparent 22%),
      radial-gradient(ellipse at center, rgba(245,230,0,.35) 0 40%, transparent 70%);
  }
  .network--back { left: 212px; top: 0; width: 344px; height: 104px; }
  .network--front { left: 640px; top: 263px; width: 506px; height: 563px; }

  /* Back cover */
  .back-title {
    position: absolute; left: 56px; top: 60px;
    font-family: "Encode Sans Condensed", sans-serif; font-weight: 200;
    font-size: 44px; letter-spacing: 0.02em; color: var(--white); line-height: 1;
  }
  .back-subtitle {
    position: absolute; left: 56px; top: 110px; width: 300px;
    font-size: 14.5px; font-weight: 300; line-height: 18.5px;
  }
  .blurb {
    position: absolute; left: 58px; top: 161px; width: 446px;
    font-size: 11.6px; font-style: italic; font-weight: 300;
    line-height: 17.4px; text-align: center;
  }
  .bio { position: absolute; left: 59px; width: 470px; }
  .bio--first { top: 359px; }
  .bio--second { top: 508px; }
  .bio__photo { position: absolute; left: 0; top: 0; width: 87px; height: 113px; }
  .bio--first .bio__photo { background: linear-gradient(160deg, var(--photo-warm-a), var(--photo-warm-b)); }
  .bio--second .bio__photo { background: linear-gradient(160deg, var(--photo-brick-a), var(--photo-brick-b)); }
  .bio__text {
    position: absolute; left: 104px; top: -2px; width: 352px;
    font-size: 11.6px; font-weight: 300; line-height: 17.4px;
  }
  .bio__text strong { font-weight: 600; }
  .publisher {
    position: absolute; font-weight: 400; letter-spacing: 0.02em;
    color: var(--brand); line-height: 1;
  }
  .publisher--back { left: 65px; top: 722px; font-size: 25px; }
  .publisher--front { left: 650px; top: 788px; font-size: 18px; }
  .isbn-space {
    position: absolute; left: 346px; top: 684px; width: 179px; height: 108px;
    background: var(--white);
  }

  /* Spine */
  .spine-title, .spine-authors {
    position: absolute; writing-mode: vertical-rl; white-space: nowrap; line-height: 1;
  }
  .spine-title {
    left: 558px; top: 52px;
    font-family: "Encode Sans Condensed", sans-serif; font-weight: 200;
    font-size: 27px; letter-spacing: 0.04em; color: var(--white);
  }
  .spine-authors { left: 561px; top: 372px; font-size: 21px; font-weight: 300; }

  /* Front cover */
  .front-authors {
    position: absolute; left: 640px; width: 506px; top: 50px;
    text-align: center; font-size: 24px; font-weight: 300; white-space: nowrap;
  }
  .front-title {
    position: absolute; left: 640px; width: 506px; top: 100px;
    text-align: center;
    font-family: "Encode Sans Condensed", sans-serif; font-weight: 200;
    font-size: 118px; letter-spacing: 0; color: var(--white); line-height: 1;
    white-space: nowrap;
  }
  .hub {
    position: absolute; left: 846px; top: 570px; width: 166px; height: 166px;
    border-radius: 50%; background: var(--navy);
    display: flex; align-items: center; justify-content: center; text-align: center;
    color: var(--white); font-weight: 600; font-size: 11.5px; line-height: 16.6px;
    padding: 0 30px;
  }
</style>
</head>
<body>
  <main class="spread">
    <!-- Back cover -->
    <div class="network network--back" role="img" aria-label="Radial network of coloured team circles joined by lines"></div>
    <h2 class="back-title">Velmorith</h2>
    <p class="back-subtitle">5 pillars to shape a people-first office</p>
    <p class="blurb">Is your organization failing to create the environment where real collaboration, innovation and speed are a natural habit and people are truly engaged? What if the real key to all this was a radical change in the way your organization is actually structured? The authors’ 15+ year experience in change initiatives, together with the outcomes of an extensive qualitative and quantitative research, led to the creation of Velmorith. Velmorith is a revolutionary organizational model based on a radial and peer- based structure of self-organized and coordinated teams that overcome the limits of the hierarchy and expands individual, team and organizational potential.</p>

    <section class="bio bio--first">
      <div class="bio__photo" role="img" aria-label="Portrait photo of Marisa Tolvengo"></div>
      <p class="bio__text"><strong>Marisa Tolvengo</strong> is a partner at Pelvaro, a global organizational development firm, a former executive in the corporate setting (including Brindle &amp; Moss and Quibbit! Inc.) and Past President of WPN Global (Worldwide Practitioner Network). She is the author of the book “Inner Compass. The Road to Renewing Guidance” and a FORAx speaker.</p>
    </section>

    <section class="bio bio--second">
      <div class="bio__photo" role="img" aria-label="Portrait photo of Lorenzo Brucani"></div>
      <p class="bio__text"><strong>Lorenzo Brucani</strong> is a partner at Pelvaro and a former manager in multinational settings. He is the co-author of the Calloway Management Journal articles “Why Your Inner Climate Shapes your Output”, “3 Ways to Lift a Gloomy Day”, “Preparing Your Inner Climate for a Holiday Break” and “An Easy Method to Ease Lasting Tension”.</p>
    </section>

    <p class="publisher publisher--back">PELVARO</p>
    <div class="isbn-space" aria-label="Space reserved for ISBN code"></div>

    <!-- Spine -->
    <p class="spine-title">Velmorith</p>
    <p class="spine-authors">Marisa Tolvengo – Lorenzo Brucani</p>

    <!-- Front cover -->
    <p class="front-authors">Marisa Tolvengo – Lorenzo Brucani</p>
    <h1 class="front-title">Velmorith</h1>
    <div class="network network--front" role="img" aria-label="Radial network of self-organizing teams drawn as coloured circles joined by lines"></div>
    <p class="hub">5 pillars to shape a people-first office</p>
    <p class="publisher publisher--front">PELVARO</p>
  </main>
</body>
</html>
```